Resposive web site in 4 languages + image gallery + logo design

We need a web page, which will work on all devices.
I have uploaded web page concept.
Company name: Praxelun
Industry/Entity Type
It Company
Logo Text
quality matters
Coding
Coded - Design and coding required
Number of Pages Required
1 page

```html
<!DOCTYPE html>
<html lang="en">
<head>
<meta charset="utf-8">
<title>Praxelun</title>
<link rel="stylesheet" href="https://fonts.googleapis.com/css2?family=Barlow:wght@400;500;600;700&display=swap">
<style>
:root{
  --wood-light:#b8642e;
  --wood-mid:#9c4f22;
  --wood-dark:#7e3d18;
  --red:#d8241c;
  --white:#ffffff;
  --card:#f4f4f4;
  --band:#e9e9e9;
  --ink:#3a3a3a;
  --muted:#8a8a8a;
  --contact:#2d2d2d;
  --field-line:#8f8f8f;
}
*{box-sizing:border-box;margin:0;padding:0}
html,body{width:1200px;height:3243px;overflow:hidden}
body{
  position:relative;
  font-family:"Barlow",Arial,sans-serif;
  color:var(--ink);
  background:linear-gradient(90deg,var(--wood-mid) 0%,var(--wood-light) 22%,var(--wood-mid) 45%,var(--wood-light) 70%,var(--wood-dark) 100%);
}
.abs{position:absolute}
.topbar{top:72px;right:134px;font-size:11px;color:var(--white);letter-spacing:.3px;display:flex;align-items:center;gap:6px}
.topbar .sq{width:10px;height:10px;background:var(--white);display:inline-block}
.page{left:132px;top:104px;width:934px;height:3014px;background:var(--white)}
.logo{left:143px;top:138px;font-size:38px;font-weight:700;color:var(--red);letter-spacing:-.5px}
.nav{right:162px;top:151px;font-size:13px;color:#555;letter-spacing:.4px;display:flex;gap:12px}
.nav span.sep{color:#999}
.hero{left:145px;top:208px;width:910px;height:534px;
  background:linear-gradient(160deg,#6f7d52 0%,#8a5a2c 30%,#a9703c 55%,#5e3a1c 80%,#3c2a1a 100%)}
.hero-box{left:445px;top:378px;width:310px;height:251px;background:rgba(20,20,20,.88);text-align:center;color:var(--white)}
.hero-box h1{font-size:45px;font-weight:700;color:var(--red);margin-top:52px;line-height:1}
.hero-box p{font-size:13px;margin-top:16px}
.hero-box .btn{display:inline-block;margin-top:16px;border:2px solid var(--white);padding:8px 16px;font-size:21px;font-weight:700;letter-spacing:.5px}
.arrow{top:486px}
.section-title{left:132px;width:934px;text-align:center;font-size:36px;font-weight:700;color:var(--red)}
.card{left:145px;width:910px;height:374px;background:var(--card)}
.card .photo{position:absolute;left:30px;top:39px;width:350px;height:234px}
.card h2{position:absolute;left:395px;top:43px;font-size:22px;font-weight:700;letter-spacing:.5px;color:#444}
.card p{position:absolute;left:395px;top:84px;width:440px;font-size:13px;line-height:23.8px;color:var(--muted)}
.card .band{position:absolute;left:0;bottom:0;width:100%;height:69px;background:var(--band);display:flex;justify-content:center;align-items:center;gap:14px;font-size:13px;color:#444}
.band .sep{color:#777}
.about-photo{left:145px;top:2248px;width:365px;height:236px;background:linear-gradient(135deg,#c9c6bd,#8e8578 50%,#7a4a26 75%,#a9a69d)}
.about-text{left:534px;top:2250px;width:510px;font-size:13px;line-height:21px;color:var(--muted)}
.about-text p+p{margin-top:18px}
.tagline{left:534px;top:2402px;font-size:24px;color:var(--red)}
.sign{left:539px;top:2450px;font-size:23px;font-weight:600;color:#333}
.contact{left:145px;top:2562px;width:910px;height:536px;background:linear-gradient(180deg,#333 0%,#262626 100%)}
.contact h2{position:absolute;left:52px;top:50px;font-size:36px;font-weight:700;color:var(--white);letter-spacing:.5px}
.contact address{position:absolute;left:52px;top:134px;font-style:normal;font-size:17px;line-height:38.5px;color:var(--white);letter-spacing:.3px}
.contact .lead{position:absolute;left:363px;top:56px;width:520px;font-size:18px;line-height:30px;color:var(--white);letter-spacing:.3px}
.field{position:absolute;left:365px;width:519px;height:46px;border:1px solid var(--field-line);font-size:10px;color:#ddd;padding:13px 10px}
.send{position:absolute;left:365px;top:456px;width:519px;height:43px;background:var(--red);color:var(--white);font-size:17px;text-align:center;line-height:43px;letter-spacing:.5px}
.footer{top:3150px;font-size:13px;color:var(--white);letter-spacing:.3px;display:flex;gap:12px}
</style>
</head>
<body>
<div class="abs topbar">EST | RUS | FIN | ENG | Social <span class="sq"></span></div>

<div class="abs page"></div>
<div class="abs logo">Praxelun</div>
<nav class="abs nav"><span>SERVICES</span><span class="sep">|</span><span>ABOUT US</span><span class="sep">|</span><span>CONTACT</span></nav>

<div class="abs hero" role="img" aria-label="Wooden garden table and chairs on a terrace"></div>
<svg class="abs arrow" style="left:168px" width="24" height="28" viewBox="0 0 24 28"><path d="M17 3 6 14l11 11" fill="none" stroke="#111" stroke-width="4"/></svg>
<svg class="abs arrow" style="left:1008px" width="24" height="28" viewBox="0 0 24 28"><path d="M7 3l11 11L7 25" fill="none" stroke="#111" stroke-width="4"/></svg>
<div class="abs hero-box">
  <h1>Woodworks</h1>
  <p>Are you interested in an estimate?</p>
  <span class="btn">GET A QUOTE</span>
</div>

<h2 class="abs section-title" style="top:816px">Our Services</h2>

<section class="abs card" style="top:897px">
  <div class="photo" role="img" aria-label="Spiral wooden staircase" style="background:linear-gradient(135deg,#3a1a10,#8a3a20 45%,#c07040 70%,#d8c8a8)"></div>
  <h2>WOODWORKS</h2>
  <p>Timber is, in essence, a natural and warm material. Wood is also relatively durable and easy to work with, which has made it a favourite of builders throughout history. Our goal is to offer suitable products and quality furniture with installation and after- sales service to all of our clients. In order to achieve this, we're ready to help our clients in all stages of construction from design to production and maintenance.</p>
  <div class="band"><span>Furniture</span><span class="sep">|</span><span>Windows</span><span class="sep">|</span><span>Doors</span><span class="sep">|</span><span>Staircases</span><span class="sep">|</span><span>Woodcarving</span><span class="sep">|</span><span>Graining</span></div>
</section>

<section class="abs card" style="top:1314px">
  <div class="photo" role="img" aria-label="Dry stacked stone wall" style="background:linear-gradient(135deg,#8c8a80,#c9c5b6 40%,#a7a394 70%,#6e6c64)"></div>
  <h2>STONEWORKS</h2>
  <p>Timber is, in essence, a natural and warm material. Wood is also relatively durable and easy to work with, which has made it a favourite of builders throughout history. Our goal is to offer suitable products and quality furniture with installation and after- sales service to all of our clients. In order to achieve this, we're ready to help our clients in all stages of construction from design to production and maintenance.</p>
  <div class="band"><span>Walls</span><span class="sep">|</span><span>Terraces</span><span class="sep">|</span><span>Paths</span><span class="sep">|</span><span>Outdoor kitchens</span><span class="sep">|</span><span>Fireplaces</span><span class="sep">|</span><span>Smokeries</span><span class="sep">|</span><span>Fences</span></div>
</section>

<section class="abs card" style="top:1732px">
  <div class="photo" role="img" aria-label="Living room with wooden floor and sofa" style="background:linear-gradient(180deg,#d8d2c6 0%,#a89a88 45%,#7a4a2c 70%,#9a5a30 100%)"></div>
  <h2>RESTORATION</h2>
  <p>Timber is, in essence, a natural and warm material. Wood is also relatively durable and easy to work with, which has made it a favourite of builders throughout history. Our goal is to offer suitable products and quality furniture with installation and after- sales service to all of our clients. In order to achieve this, we're ready to help our clients in all stages of construction from design to production and maintenance.</p>
  <div class="band"><span>Furniture</span><span class="sep">|</span><span>Windows</span><span class="sep">|</span><span>Doors</span><span class="sep">|</span><span>Staircases</span><span class="sep">|</span><span>Floors</span><span class="sep">|</span><span>Special Projects</span></div>
</section>

<h2 class="abs section-title" style="top:2156px">ABOUT US</h2>
<div class="abs about-photo" role="img" aria-label="Wooden bench beside a stone sphere"></div>
<div class="abs about-text">
  <p>Praxelun is a company whose business operations include making wooden products, restoration and building structures from natural stone.</p>
  <p>All of our products are made by craftsmen and specialists who have extensive experience and knowledge in their fields.The products we offer are always handmade and we take therequests and ideas of the specific client into account. We always strive to achieve the best possible quality.</p>
</div>
<div class="abs tagline">Quality Matters,</div>
<div class="abs sign">Praxelun</div>

<section class="abs contact">
  <h2>CONTACT</h2>
  <address>Kaseke 12 | &nbsp;10115 Tallinn<br>ESTONIA<br>Telephone: +372 55 18230<br>E-mail: hello@praxelun.ee</address>
  <div class="lead">PLEASE FILL IN THE FOLLOWING FIELDS IF YOU WOULD LIKE A PRICE QUOTE</div>
  <div class="field" style="top:138px">Name</div>
  <div class="field" style="top:197px">E-mail</div>
  <div class="field" style="top:257px">Phone</div>
  <div class="field" style="top:318px;height:119px">Message</div>
  <div class="send">SEND</div>
</section>

<div class="abs footer" style="left:132px"><span>SERVICES</span><span>|</span><span>ABOUT US</span><span>|</span><span>CONTACT</span></div>
<div class="abs footer" style="right:132px"><span>© 2016 COMPANY NAME &nbsp;|&nbsp; ALL RIGHTS RESERVED</span></div>
</body>
</html>
```